National Mission Critical Construction Contractor needs Stationery Design to make a bold statement

We are a small commercial construction company, working primarily in mission critical facilities across the U.S.. We have exciting corporate changes going an and a new logo and office space so we need new stationery. The final design should incorporate our new logo and invoke a fresh, high-tech feel while looking simple and modern.

Industry/Entity Type

Construction

Contact Information for Business Card

We are required to list our state licensing qualifications on the back of our card.

Font styles to use
Sans Serif

Requirements
Must have
• We need to have a design for second page of stationery, envelopes both standard and with a window and for a 3 x 4 notepad.

```html
<!DOCTYPE html>
<html lang="en">
<head>
<meta charset="utf-8">
<title>Northgate Build — Stationery Set</title>
<link href="https://fonts.googleapis.com/css2?family=Open+Sans:wght@400;600&display=swap" rel="stylesheet">
<style>
:root{
  --board:#e4e4e4;
  --paper:#f4f4f2;
  --white:#ffffff;
  --brand:#0a6fba;
  --fresh:#8dc63f;
  --ink:#4a4a4a;
  --faint:rgba(10,111,186,.07);
  --shadow:0 1px 3px rgba(0,0,0,.22);
}
*{margin:0;padding:0;box-sizing:border-box}
html,body{width:1200px;height:889px;overflow:hidden}
body{background:var(--board);font-family:"Open Sans",Arial,sans-serif;color:var(--ink);position:relative}
.sheet{position:absolute;box-shadow:var(--shadow);overflow:hidden}
.paper{background:var(--paper)}
.white{background:var(--white)}
.blue{background:var(--brand);color:var(--white)}

.brand{display:flex;flex-direction:column;align-items:center;gap:4px;position:absolute}
.brand .dot{border-radius:50%;background:var(--brand)}
.brand .name{font-weight:600;letter-spacing:.06em;text-transform:uppercase;color:var(--brand);white-space:nowrap}
.blue .brand .dot{background:var(--white)}
.blue .brand .name{color:var(--white)}

.decor{position:absolute;border-radius:50%;border:8px solid var(--faint)}

/* letterhead */
.letterhead{left:26px;top:22px;width:344px;height:486px}
.letter{position:absolute;left:35px;top:155px;width:282px;font-size:5.2px;line-height:8.2px}
.letter .salute{font-size:9px;margin-bottom:16px}
.letter p{margin-bottom:8px}
.sign{width:50px;height:18px;background:linear-gradient(90deg,#cfcfcf,#e8e8e8);margin:4px 0 6px}
.foot{position:absolute;left:0;right:0;text-align:center;font-size:5.6px;line-height:11px}
.foot b{color:var(--brand);font-weight:600}

/* business cards */
.card-front{left:602px;top:31px;width:151px;height:86px}
.card-front .info{position:absolute;left:85px;top:16px;font-size:3.6px;line-height:5.4px}
.card-front .who{font-size:5.4px;font-weight:600;color:var(--brand);line-height:6px}
.card-back{left:774px;top:30px;width:151px;height:86px}
.card-back h4{font-size:4.8px;font-weight:600;text-align:center;margin-top:5px}
.lic{position:absolute;left:10px;right:10px;top:15px;display:flex;justify-content:space-between;font-size:3.4px;line-height:4.2px}

/* envelopes */
.env{width:386px;height:176px}
.flap{position:absolute;left:0;right:0;top:0;height:64px;border-radius:0 0 26px 26px / 0 0 18px 18px}
.flap.brand-blue{background:var(--brand)}
.flap.brand-green{background:var(--fresh)}
.flap .url{position:absolute;left:0;right:0;top:43px;text-align:center;font-size:5.4px;color:var(--white)}
.flap .mark{position:absolute;left:50%;top:18px;width:18px;height:18px;margin-left:-9px;border-radius:50%;background:var(--white)}
.ret{position:absolute;left:15px;bottom:13px;font-size:5.6px;line-height:8px}
.window{position:absolute;left:24px;top:64px;width:121px;height:46px;border-radius:5px;background:linear-gradient(#e9e9e9,#d3d3d3);border:1px solid #c6c6c6}

/* notepads */
.note-v{width:239px;height:320px}
.note-h{width:318px;height:240px}
.caption{position:absolute;font-size:7px;color:rgba(255,255,255,.55);text-align:center}
</style>
</head>
<body>

<!-- Letterhead -->
<section class="sheet paper letterhead">
  <div class="decor" style="left:80px;top:160px;width:210px;height:210px"></div>
  <div class="brand" style="left:0;right:0;top:22px">
    <span class="dot" style="width:30px;height:30px"></span>
    <span class="name" style="font-size:11px">Northgate Build</span>
  </div>
  <div class="letter">
    <div class="salute">Dear Mr. Carter,</div>
    <p>Lorem ipsum dolor sit amet, consectetur adipiscing elit. Donec orci purus, luctus vitae dignissim eu, iaculis sed purus. Vivamus faucibus, ipsum nec aliquet viverra, leo mauris condimentum ligula, sit amet sagittis enim ligula quis arcu. Nam egestas tortor id nisi porttitor mattis. In tortor ante, ultricies in suscipit a, tempus non massa. Vivamus et auctor mi. Fusce vel massa nulla. Phasellus nec eros mauris, et scelerisque orci.</p>
    <p>Donec malesuada orci vitae nulla accumsan porta a id massa. Quisque accumsan iaculis magna sit amet fringilla. Maecenas consequat, magna eget tincidunt semper, odio nibh rutrum mi, id feugiat ante nisi eu risus. Vestibulum nunc orci, rhoncus a placerat in, ultricies in mi. Cras mattis varius eros, vel fringilla nisi suscipit eget. Quisque scelerisque sagittis nulla at porttitor.</p>
    <p>Sed id augue vitae urna euismod commodo aliquet a quam. Pellentesque arcu velit, cursus et malesuada ut, consequat et diam. Nullam erat sem, rhoncus id ullamcorper vitae, rhoncus et arcu. In ultricies ultricies nulla, ut rutrum nisi iaculis at. Donec eu magna a metus ornare faucibus. Fusce aliquet faucibus ultricies. Morbi semper, est id tincidunt gravida, sem arcu adipiscing lacus, ac bibendum nulla leo eu purus. Quisque nec diam sed risus consectetur a cursus quis nibh.</p>
    <p>It is a long established fact that a reader will be distracted by the readable content of a page when looking at its layout. The point of using Lorem Ipsum is that it has a more-or-less normal distribution of letters, as opposed to using 'Content here, content here', making it look like readable English.</p>
    <div style="margin-top:14px">Sincerely,</div>
    <div class="sign" role="img" aria-label="Handwritten signature"></div>
    <div>Daniel Reyes<br>CEO / Founder</div>
  </div>
  <div class="foot" style="bottom:10px">412 Cedar Hollow Road, Fairbanks, Alaska 99701<br>
    <b>☎</b> 907 555 0142 &nbsp;<b>▯</b> 907 555 0187 &nbsp;<b>▬</b> 907 555 0163 &nbsp;<b>✉</b> hello@northgatebuild.com &nbsp;<b>●</b> www.northgatebuild.com</div>
</section>

<!-- Business card front -->
<section class="sheet white card-front">
  <div class="brand" style="left:10px;top:27px">
    <span class="dot" style="width:16px;height:16px"></span>
    <span class="name" style="font-size:6.4px">Northgate Build</span>
  </div>
  <div class="info">
    <div class="who">Daniel Reyes</div>
    <div style="color:var(--brand);margin-bottom:2px">CEO / Founder</div>
    412 Cedar Hollow Road<br>Fairbanks, Alaska 99701<br>
    ☎ 907 555 0142<br>▯ 907 555 0187<br>▬ 907 555 0163<br>✉ hello@northgatebuild.com<br>● www.northgatebuild.com
  </div>
</section>

<!-- Business card back -->
<section class="sheet blue card-back">
  <div class="decor" style="left:48px;top:18px;width:60px;height:60px;border-color:rgba(255,255,255,.08);border-width:5px"></div>
  <h4>State Contracting Licenses</h4>
  <div class="lic">
    <div>Alabama<br>Arizona — Northgate Build, LLC<br>Florida<br>Georgia<br>Idaho<br>Kansas, Johnson County<br>Louisiana<br>Mississippi<br>Nebraska, Omaha<br>North Carolina<br>South Carolina<br>Tennessee<br>Virginia</div>
    <div>41208<br>ROC 218844<br>CGC 071523<br>GCC 004418<br>RCE 31570<br>21-6630<br>52187<br>15032<br>LIC 1730482<br>61045<br>G 120937<br>00061388<br>2705 148822A</div>
  </div>
</section>

<!-- Envelope backs -->
<section class="sheet paper env" style="left:386px;top:142px">
  <div class="flap brand-blue"><span class="mark"></span><span class="url">www.northgatebuild.com</span></div>
</section>
<section class="sheet paper env" style="left:788px;top:142px">
  <div class="flap brand-green"><span class="mark"></span><span class="url">www.northgatebuild.com</span></div>
</section>

<!-- Envelope fronts -->
<section class="sheet paper env" style="left:386px;top:332px">
  <div class="decor" style="left:212px;top:12px;width:170px;height:170px"></div>
  <div class="brand" style="left:15px;top:14px;align-items:flex-start">
    <span class="dot" style="width:22px;height:22px;margin-left:32px"></span>
    <span class="name" style="font-size:8.6px">Northgate Build</span>
  </div>
  <div class="ret">412 Cedar Hollow Road<br>Fairbanks, Alaska 99701</div>
</section>
<section class="sheet paper env" style="left:788px;top:332px">
  <div class="decor" style="left:218px;top:10px;width:170px;height:170px"></div>
  <div class="brand" style="left:25px;top:11px;align-items:flex-start">
    <span class="dot" style="width:22px;height:22px;margin-left:32px"></span>
    <span class="name" style="font-size:8.6px">Northgate Build</span>
  </div>
  <div class="window"></div>
  <div class="ret" style="left:25px">412 Cedar Hollow Road<br>Fairbanks, Alaska 99701</div>
</section>

<!-- Vertical notepad -->
<section class="sheet blue note-v" style="left:25px;top:534px">
  <div class="brand" style="left:0;right:0;top:122px;gap:8px">
    <span class="dot" style="width:44px;height:44px"></span>
    <span class="name" style="font-size:15px">Northgate Build</span>
  </div>
</section>
<section class="sheet white note-v" style="left:274px;top:534px">
  <div class="decor" style="left:40px;top:108px;width:150px;height:150px"></div>
  <div class="brand" style="left:0;right:0;top:12px">
    <span class="dot" style="width:22px;height:22px"></span>
    <span class="name" style="font-size:8.6px">Northgate Build</span>
  </div>
  <div class="foot" style="bottom:8px;font-size:5.6px">412 Cedar Hollow Road, Fairbanks, Alaska 99701 &nbsp;<b>P:</b> 907 555 0142<br>
    <b>M:</b> 907 555 0187 <b>F:</b> 907 555 0163 <b>E:</b> hello@northgatebuild.com <b>W:</b> northgatebuild.com</div>
</section>
<div class="caption" style="left:25px;top:858px;width:239px">Vertical note pad Front 3x4</div>
<div class="caption" style="left:274px;top:855px;width:239px">Vertical note pad Inner 3x4</div>

<!-- Horizontal notepad -->
<section class="sheet blue note-h" style="left:526px;top:614px">
  <div class="brand" style="left:0;right:0;top:82px;gap:8px">
    <span class="dot" style="width:44px;height:44px"></span>
    <span class="name" style="font-size:15px">Northgate Build</span>
  </div>
</section>
<section class="sheet white note-h" style="left:857px;top:614px">
  <div class="decor" style="left:175px;top:82px;width:180px;height:180px"></div>
  <div class="brand" style="left:0;right:0;top:12px">
    <span class="dot" style="width:26px;height:26px"></span>
    <span class="name" style="font-size:10px">Northgate Build</span>
  </div>
  <div class="foot" style="bottom:8px;font-size:5.6px">412 Cedar Hollow Road, Fairbanks, Alaska 99701 &nbsp;<b>P:</b> 907 555 0142<br>
    <b>M:</b> 907 555 0187 <b>F:</b> 907 555 0163 <b>E:</b> hello@northgatebuild.com <b>W:</b> northgatebuild.com</div>
</section>
<div class="caption" style="left:526px;top:860px;width:318px">Horizontal notepad Front 3x4</div>
<div class="caption" style="left:857px;top:857px;width:318px">Horizontal notepad Inner 3x4</div>

</body>
</html>
```